Corvane Holdings , new business card design

investment firm with corporate clients . need double sided business card , vertical and horizontal options ,logo must be clear. prefer pantone colors only and sharp design. website also www.corvane.ae

Khalid Bin Tarrafi
Managing Director
Tel. +971 4 387 2940
Mobile +971 50 518 2403
khalid@corvane.ae
Q-Span Plaza, officw 18-B07, Warqa Gardens, Dubai

Contact Information for Business Card

Khalid Bin Tarrafi
Managing Director

Font styles to use
Serif

Colors

Designer to choose colors to be used in the design.

```html
<!DOCTYPE html>
<html lang="en">
<head>
<meta charset="utf-8">
<title>Corvane Holdings – Business Card</title>
<link href="https://fonts.googleapis.com/css2?family=Jost:wght@500;600&family=Roboto:wght@300;400;500&display=swap" rel="stylesheet">
<style>
  :root {
    --page-bg: #e9e6e1;
    --card-white: #fbfbfb;
    --brand-blue: #4d7ea8;
    --brand-blue-deep: #3f6d96;
    --ink: #1f1f1f;
    --ink-soft: #4a4a4a;
  }
  * { box-sizing: border-box; margin: 0; padding: 0; }
  html, body { width: 1200px; height: 886px; overflow: hidden; background: var(--page-bg); }
  .canvas {
    position: relative; width: 1200px; height: 886px;
    display: flex; align-items: center; justify-content: center; gap: 60px;
  }
  .card {
    position: relative; width: 520px; height: 297px;
    box-shadow: 0 6px 18px rgba(0,0,0,0.18);
  }
  /* Front */
  .card--front { background: var(--card-white); }
  .front__brand {
    position: absolute; top: 38px; right: 36px;
    font-family: "Roboto", sans-serif; font-weight: 300;
    font-size: 22px; letter-spacing: 5px; text-transform: uppercase;
    color: var(--brand-blue);
  }
  .front__rule {
    position: absolute; top: 130px; left: 34px; right: 36px;
    height: 1px; background: var(--brand-blue);
  }
  .front__identity { position: absolute; left: 34px; top: 84px; }
  .front__name {
    font-family: "Jost", sans-serif; font-weight: 600;
    font-size: 21px; color: var(--brand-blue); line-height: 1.1;
  }
  .front__title {
    font-family: "Jost", sans-serif; font-weight: 600;
    font-size: 13px; color: var(--ink); margin-top: 2px;
  }
  .front__contacts {
    position: absolute; left: 34px; bottom: 30px;
    list-style: none;
    font-family: "Roboto", sans-serif; font-weight: 400;
    font-size: 12px; color: var(--ink-soft); line-height: 1.6;
  }
  .front__contacts li { display: flex; align-items: center; gap: 8px; }
  .front__contacts svg { width: 11px; height: 11px; flex: none; }
  .front__address {
    position: absolute; right: 36px; bottom: 30px; text-align: right;
    font-family: "Roboto", sans-serif; font-weight: 400;
    font-size: 12px; color: var(--ink-soft); line-height: 1.5;
  }
  .front__web {
    color: var(--brand-blue); font-weight: 500; letter-spacing: 3px; margin-top: 3px;
  }
  /* Back */
  .card--back {
    background: linear-gradient(135deg, #5a8ab3 0%, var(--brand-blue) 45%, var(--brand-blue-deep) 100%);
    display: flex; align-items: center; justify-content: center; gap: 14px;
  }
  .back__mark { width: 14px; height: 14px; background: #ffffff; }
  .back__brand {
    font-family: "Roboto", sans-serif; font-weight: 300;
    font-size: 30px; letter-spacing: 8px; text-transform: uppercase; color: #ffffff;
  }
</style>
</head>
<body>
<main class="canvas">
  <section class="card card--front" aria-label="Card front">
    <div class="front__brand">Corvane Holdings</div>
    <div class="front__identity">
      <h1 class="front__name">Khalid Bin Tarrafi</h1>
      <p class="front__title">Managing Director</p>
    </div>
    <div class="front__rule"></div>
    <ul class="front__contacts">
      <li>
        <svg viewBox="0 0 12 12" aria-hidden="true"><path d="M2.5 1 L4.5 1 L5.2 3.6 L3.9 4.6 Q5 7 7.4 8.1 L8.4 6.8 L11 7.5 L11 9.5 Q10.5 11 9 11 Q1 10 1 3 Q1 1.5 2.5 1 Z" fill="#4d7ea8"/></svg>
        +971 4 387 2940
      </li>
      <li>
        <svg viewBox="0 0 12 12" aria-hidden="true"><rect x="3" y="0.8" width="6" height="10.4" rx="1" fill="none" stroke="#4d7ea8" stroke-width="1.2"/><circle cx="6" cy="9.3" r="0.7" fill="#4d7ea8"/></svg>
        +971 50 518 2403
      </li>
      <li>
        <svg viewBox="0 0 12 12" aria-hidden="true"><rect x="0.6" y="2" width="10.8" height="8" fill="#4d7ea8"/><path d="M1 2.5 L6 6.5 L11 2.5" fill="none" stroke="#fff" stroke-width="1"/></svg>
        khalid@corvane.ae
      </li>
    </ul>
    <div class="front__address">
      <p>Q-Span Plaza, officw 18-B07</p>
      <p>Warqa Gardens, Dubai</p>
      <p class="front__web">www.corvane.ae</p>
    </div>
  </section>

  <section class="card card--back" aria-label="Card back">
    <span class="back__mark"></span>
    <span class="back__brand">Corvane Holdings</span>
  </section>
</main>
</body>
</html>
```